Tandem Pocket Apps Needs banners for webpage

We need a top banner. We are a mobile app developer for the Hospitality Industry. We are developing a Loyalty Program with the trade name TandemPerks. The banner will be used on our loyalty page inside our website.Please see www.tandempocketapps.example to understand our theme. The banner should be 1700 X 470.

Please see the attached banner. This is from a competitor website.Please use it as a model and make changes...... make it unique to TandemPocket. I need to convey the same message as this banner. Same statistics. Same setting (restaurant).

I have added a purchased vector file for the restaurant setting. I noticed many are struggling and using stock art which I don't like.Work with the background color. Make it more playful--pastels--less formal. Be creative!

Do not wait till that last day of the contest to submit. I might take the first design I like and proceed. The sooner you post a design, the better direction I can give you.
Updates

Project Deadline Extended
Reason: Not getting any designs I can work with yet. Please give me ideas.

All, Please re-read the brief. I have changed the banner project. It will be much easier but I need it quickly.

Now that I have made this banner much easier, I would like to wrap this contest up. Don't wait till the last day to post designs. The first design I like I will go with and close the project. Be creative, colorful, imaginative! Good luck. Marcus Hennet Tandem Pocket Apps, LLC mhennet@

All. See the vector file that I just purchased for the background image. Can you try different background colors. I still need the other content showing the percentages of loyalty. I do not want the rocket ship!

All, I have updated the brief. I have included a vector file that has a perfect restaurant scene. Please be creative and work with colors in this scene. Also be creative with the information in the circles showing the metrics of loyalty. Do not use the Rocket. If you find another idea to replace the rocket, that's fine. Or, just leave it off. Please make this banner unique!

Target Market(s)

Hospitality Industry.

Industry/Entity Type

Restaurant

Requirements
Must have
• Banner should be beautiful.. Image of diners at restaurant along with the statistics and message "Boost Sales".
Nice to have
• Our banner should convey the same message as the attached but we must re-design because the attached banner belongs to another company.
Should not have
• Do not re-use any of the images in the attached banner. This is from my competitor. Do not use a rocket for "Boost Sales" image.

```html
<!DOCTYPE html>
<html lang="en">
<head>
<meta charset="utf-8">
<title>Boost Sales – Loyal Guest vs. Average Guest</title>
<link rel="stylesheet" href="https://fonts.googleapis.com/css2?family=Oregano&family=Lato:wght@400;700&display=swap">
<style>
  :root {
    --scene-peach: #fbd9c4;
    --scene-blush: #f7c6cf;
    --scene-mint: #c9ead9;
    --scene-butter: #fbeab8;
    --scene-lilac: #dcd3f0;
    --cap-white: rgba(255, 255, 255, 0.92);
    --badge-white: #ffffff;
    --accent-orange: #ea6a1c;
    --ink: #2a2a2a;
  }
  html, body {
    margin: 0;
    padding: 0;
    width: 1200px;
    height: 331px;
    overflow: hidden;
    background: #ffffff;
  }
  .banner {
    position: relative;
    width: 1200px;
    height: 331px;
    overflow: hidden;
  }
  .restaurant-scene {
    position: absolute;
    inset: 0;
    background:
      radial-gradient(ellipse 420px 260px at 12% 40%, var(--scene-blush) 0%, transparent 70%),
      radial-gradient(ellipse 380px 240px at 50% 70%, var(--scene-butter) 0%, transparent 70%),
      radial-gradient(ellipse 420px 280px at 88% 45%, var(--scene-mint) 0%, transparent 70%),
      radial-gradient(ellipse 500px 200px at 50% 0%, var(--scene-lilac) 0%, transparent 75%),
      linear-gradient(180deg, var(--scene-peach) 0%, #f6c9ae 100%);
  }
  .headline-cap {
    position: absolute;
    left: 392px;
    top: -110px;
    width: 416px;
    height: 208px;
    border-radius: 50%;
    background: var(--cap-white);
  }
  .headline {
    position: absolute;
    left: 0;
    right: 0;
    top: 10px;
    display: flex;
    justify-content: center;
    align-items: center;
    gap: 8px;
  }
  .headline-mark {
    width: 34px;
    height: 34px;
    border-radius: 50%;
    background: var(--accent-orange);
    flex: none;
  }
  .headline-text {
    display: flex;
    flex-direction: column;
    align-items: flex-start;
  }
  .headline-title {
    font-family: "Lato", sans-serif;
    font-weight: 700;
    font-size: 26px;
    line-height: 1;
    color: var(--ink);
  }
  .headline-subtitle {
    font-family: "Lato", sans-serif;
    font-size: 10px;
    line-height: 1;
    color: var(--ink);
    margin-top: 12px;
    padding-left: 8px;
  }
  .stat-badge {
    position: absolute;
    top: 164px;
    width: 176px;
    height: 138px;
  }
  .badge-frame {
    position: absolute;
    inset: 0;
  }
  .stat-content {
    position: absolute;
    inset: 0;
    display: flex;
    flex-direction: column;
    align-items: center;
    justify-content: center;
    font-family: "Oregano", cursive;
    color: var(--ink);
    text-align: center;
  }
  .stat-label {
    font-size: 12px;
    line-height: 1.1;
  }
  .stat-value {
    font-size: 52px;
    line-height: 1;
    color: var(--accent-orange);
    margin: 8px 0 10px;
    -webkit-text-stroke: 1px var(--accent-orange);
  }
  .stat-icon {
    margin: 10px 0 10px;
  }
  .badge-visits { left: 244px; }
  .badge-spend { left: 516px; }
  .badge-worth { left: 782px; }
</style>
</head>
<body>
  <main class="banner">
    <div class="restaurant-scene" role="img" aria-label="Pastel illustrated restaurant scene with diners relaxing at tables and sofas"></div>

    <div class="headline-cap"></div>
    <header class="headline">
      <span class="headline-mark"></span>
      <div class="headline-text">
        <span class="headline-title">Boost Sales</span>
        <span class="headline-subtitle">Loyal Guest vs. Average Guest</span>
      </div>
    </header>

    <section class="stat-badge badge-visits">
      <svg class="badge-frame" width="176" height="138" viewBox="0 0 176 138">
        <path d="M24 4 Q88 -2 152 4 Q152 20 171 22 Q176 69 171 116 Q152 118 152 134 Q88 140 24 134 Q24 118 5 116 Q0 69 5 22 Q24 20 24 4 Z"
              fill="var(--badge-white)" stroke="var(--accent-orange)" stroke-width="3"/>
      </svg>
      <div class="stat-content">
        <span class="stat-label">Loyal Guests Visit About</span>
        <span class="stat-value">32%</span>
        <span class="stat-label">More Than Average Guests</span>
      </div>
    </section>

    <section class="stat-badge badge-spend">
      <svg class="badge-frame" width="176" height="138" viewBox="0 0 176 138">
        <path d="M24 4 Q88 -2 152 4 Q152 20 171 22 Q176 69 171 116 Q152 118 152 134 Q88 140 24 134 Q24 118 5 116 Q0 69 5 22 Q24 20 24 4 Z"
              fill="var(--badge-white)" stroke="var(--accent-orange)" stroke-width="3"/>
      </svg>
      <div class="stat-content">
        <span class="stat-label">Loyal Guests Spend About</span>
        <span class="stat-value">22%</span>
        <span class="stat-label">More Than Average Guests</span>
      </div>
    </section>

    <section class="stat-badge badge-worth">
      <svg class="badge-frame" width="176" height="138" viewBox="0 0 176 138">
        <path d="M24 4 Q88 -2 152 4 Q152 20 171 22 Q176 69 171 116 Q152 118 152 134 Q88 140 24 134 Q24 118 5 116 Q0 69 5 22 Q24 20 24 4 Z"
              fill="var(--badge-white)" stroke="var(--accent-orange)" stroke-width="3"/>
      </svg>
      <div class="stat-content">
        <span class="stat-label">1 Loyal Guest =</span>
        <svg class="stat-icon" width="36" height="46" viewBox="0 0 36 46" aria-hidden="true">
          <circle cx="18" cy="10" r="9" fill="var(--accent-orange)"/>
          <path d="M2 46 V30 Q2 21 11 21 H25 Q34 21 34 30 V46 Z" fill="var(--accent-orange)"/>
          <path d="M15 21 L18 34 L21 21 Z" fill="var(--badge-white)"/>
        </svg>
        <span class="stat-label">10 Average Guests</span>
      </div>
    </section>
  </main>
</body>
</html>
```